*YO!!! Designers Needed!!* Front Page Cover Needed for a $$Billion Dollar$$ Company

We are a manufacturer of aluminum electrolytic capacitors. We are looking to create a front page cover that will be used on our annual report. We are a publicly listed company and work with many Meridex 400 companies, so your work will be viewed by the BIG GUNS and EXECUTIVES around the WORLD! If selected, you may be selected for additional work.

The front page cover should be unique. If elegance, modern, bling, and creativity somehow got together and had a child, that's what the cover page would look like!

Inspired Examples attached. Check them out!

www.brovanta.com

Font styles to use
Sans Serif

Requirements
Must have
• 1. Must include the attached logo. Logo size, color, and placement are at your discretion.

2. Should include the text, '2020 Annual Report'

3. The design should incorporate the use of foil and/or be embossed. The foil can be part of the design or can be the full page. See various examples attached for reference.

4. Shall be in A4 size and vertical orientation.
Nice to have
• Feel free to add any icons or stock photos (for example capacitors or circuit boards) if needed.

Be creative here and don't be afraid to be bold! The end product will be printed and budget is not a limiting factor, so feel free to make it extravagant if needed.

Our slogan is "Think Ahead". This slogan can or cannot be part of the theme.

```html
<!DOCTYPE html>
<html lang="en">
<head>
<meta charset="utf-8">
<title>Brovanta — 2020 Annual Report Cover</title>
<link rel="stylesheet" href="https://fonts.googleapis.com/css2?family=Montserrat:wght@400;600&display=swap">
<style>
  :root {
    --stage: #2a2622;
    --cover-black: #0b0b0c;
    --cover-edge: #1c1b1a;
    --quilt-gold: #6b5530;
    --foil-light: #f4efdc;
    --foil-mid: #d9c99a;
    --foil-deep: #a88f5a;
    --frame-line: #e9e6df;
    --ink: #2b2722;
  }
  * { margin: 0; padding: 0; box-sizing: border-box; }
  html, body {
    width: 1200px;
    height: 789px;
    overflow: hidden;
    background: var(--stage);
  }
  .canvas {
    position: relative;
    width: 1200px;
    height: 789px;
    display: flex;
    align-items: center;
    justify-content: center;
  }
  .cover {
    position: relative;
    width: 523px;
    height: 740px;
    background: var(--cover-black);
    overflow: hidden;
    box-shadow: 0 14px 40px rgba(0,0,0,0.55);
  }
  .quilt-pattern {
    position: absolute;
    inset: 0;
    background:
      radial-gradient(ellipse at 50% 45%, rgba(60,50,35,0.55) 0%, rgba(20,18,16,0.2) 55%, transparent 80%),
      linear-gradient(160deg, var(--cover-edge) 0%, var(--cover-black) 60%, #050505 100%);
  }
  .foil-splash {
    position: absolute;
    left: 92px;
    top: 180px;
    width: 345px;
    height: 320px;
    border-radius: 46% 54% 42% 58% / 52% 44% 56% 48%;
    background: radial-gradient(ellipse at 55% 55%,
      var(--foil-light) 0%, var(--foil-mid) 45%, var(--foil-deep) 75%, rgba(168,143,90,0) 100%);
  }
  .title-frame {
    position: absolute;
    left: 112px;
    top: 190px;
    width: 300px;
    height: 300px;
  }
  .brand-block {
    position: absolute;
    left: 0;
    right: 0;
    top: 262px;
    text-align: center;
    color: var(--ink);
    font-family: "Montserrat", sans-serif;
  }
  .brand-name {
    font-size: 44px;
    font-weight: 600;
    letter-spacing: 1px;
    line-height: 1;
  }
  .brand-slogan {
    margin-top: 6px;
    padding-left: 120px;
    font-size: 10px;
    font-weight: 400;
    letter-spacing: 2px;
    text-transform: uppercase;
  }
  .report-block {
    position: absolute;
    left: 0;
    right: 0;
    top: 372px;
    text-align: center;
    color: var(--ink);
    font-family: "Montserrat", sans-serif;
  }
  .report-year {
    font-size: 40px;
    font-weight: 600;
    letter-spacing: 18px;
    padding-left: 18px;
    line-height: 1;
  }
  .report-label {
    margin-top: 6px;
    font-size: 11px;
    font-weight: 400;
    letter-spacing: 5px;
    text-transform: uppercase;
  }
</style>
</head>
<body>
  <main class="canvas">
    <section class="cover">
      <div class="quilt-pattern" role="img" aria-label="Black quilted diamond pattern with fine gold stitching lines and dots"></div>
      <div class="foil-splash" role="img" aria-label="Gold foil brush-stroke splash"></div>
      <svg class="title-frame" viewBox="0 0 300 300" aria-hidden="true">
        <rect x="1" y="1" width="298" height="298" fill="none" stroke="var(--frame-line)" stroke-width="1.5"/>
      </svg>
      <div class="brand-block">
        <div class="brand-name">Brovanta</div>
        <div class="brand-slogan">Think Ahead.</div>
      </div>
      <div class="report-block">
        <div class="report-year">2020</div>
        <div class="report-label">Annual Report</div>
      </div>
    </section>
  </main>
</body>
</html>
```